Website Design for Hulls for Heroes

Please design and code a new website.
Here are the sites I like best:
http://www.sailbrisk.com/alternate/
http://www.wheelsforhonor.org
Please make it similar. This is NOT a car donation site. It's a boat donation site. I just like this sites above as a lead generation sites.
Old site:
http://hullsforheroes.org
Updates
Coding
Coded - Design and coding required
Number of Pages Required
1 page
Look and feel
Each slider illustrates characteristics of the customer's brand and the style your logo design should communicate.

```html
<!DOCTYPE html>
<html lang="en">
<head>
<meta charset="utf-8">
<title>Hulls for Heroes – Donate Your Boat</title>
<link href="https://fonts.googleapis.com/css2?family=Open+Sans:wght@400;600;700;800&display=swap" rel="stylesheet">
<style>
:root{
  --navy:#0d2a7a;
  --navy-deep:#0a1f5c;
  --red:#9b1c1c;
  --red-bright:#b3201f;
  --white:#ffffff;
  --ink:#1f2a44;
  --muted:#5a5f6e;
  --line:#d7dae3;
  --soft:#f3f4f7;
}
*{box-sizing:border-box;margin:0;padding:0}
html,body{width:1200px;height:2786px;overflow:hidden}
body{font-family:"Open Sans",Arial,sans-serif;color:var(--ink);background:var(--white);position:relative}
.abs{position:absolute}

/* header */
.site-header{left:0;top:0;width:1200px;height:160px;background:linear-gradient(100deg,#1b2d6b 0%,#3a4f8f 35%,#9c3a44 65%,#c9cbd6 100%)}
.brand{left:40px;top:62px;display:flex;align-items:center;gap:16px}
.brand-dot{width:34px;height:34px;border-radius:50%;background:var(--white)}
.brand-name{font-weight:800;font-size:32px;color:var(--white);letter-spacing:.5px;text-transform:uppercase;white-space:nowrap}
.call-box{display:flex;align-items:center;gap:14px;color:var(--white);white-space:nowrap}
.call-box .ring{width:66px;height:66px;flex:none;border:3px solid var(--white);border-radius:50%;display:flex;align-items:center;justify-content:center}
.call-box .lead{font-weight:800;font-size:20px;line-height:1}
.call-box .num{font-weight:800;font-size:32px;line-height:1.05}
.call-box .note{font-weight:700;font-size:12.5px}
.header-call{left:805px;top:24px}

/* nav */
.main-nav{left:0;top:160px;width:1200px;height:42px;background:var(--red)}
.main-nav a{position:absolute;top:11px;color:var(--white);font-weight:800;font-size:16px;text-decoration:none}
.donate-tab{left:793px;top:158px;width:373px;height:46px;background:var(--white);border:2px solid var(--line);color:var(--red);font-weight:800;font-size:19px;display:flex;align-items:center;justify-content:center}

/* hero */
.hero-media{left:0;top:202px;width:1200px;height:490px;background:linear-gradient(90deg,#6d6555 0%,#b9b4a8 30%,#e9eaee 55%,#f4f5f8 100%)}
.donate-form{left:793px;top:210px;width:358px;height:482px;background:var(--navy);padding:30px 20px}
.donate-form h2{color:var(--white);font-size:17px;font-weight:700;text-align:center;margin-bottom:14px}
.field-row{display:flex;gap:10px;margin-bottom:10px}
.field{flex:1;height:34px;background:var(--white);font-size:13px;font-weight:600;color:var(--ink);padding:8px 8px;position:relative}
.field.select::after{content:"";position:absolute;right:12px;top:14px;border:6px solid transparent;border-top-color:#666}
.btn-donate{width:154px;height:42px;background:var(--red-bright);color:var(--white);font-weight:800;font-size:16px;display:flex;align-items:center;justify-content:center;margin-top:6px}

/* promo band */
.promo-band{left:0;top:692px;width:1200px;height:200px;background:var(--red)}
.promo-badge{left:84px;top:678px;width:403px;height:232px;background:var(--navy);clip-path:polygon(8% 0,92% 0,100% 12%,100% 88%,92% 100%,8% 100%,0 88%,0 12%);display:flex;flex-direction:column;align-items:center;justify-content:center;color:var(--white);text-align:center}
.promo-badge .s{font-weight:800;font-size:27px}
.promo-badge .b{font-weight:800;font-size:58px;line-height:1.1;color:#c7d0a0;letter-spacing:2px}
.benefit{width:150px;text-align:center;color:var(--white);font-weight:700;font-size:14px;line-height:1.25}
.benefit svg{display:block;margin:0 auto 12px}

/* section titles */
.section-title{width:1200px;left:0;display:flex;align-items:center;justify-content:center;gap:24px;font-weight:800;font-size:30px;color:var(--navy)}
.section-title::before,.section-title::after{content:"";width:95px;height:2px;background:#9aa0b4}
.section-title em{font-style:normal;color:var(--red-bright)}

/* steps */
.step{width:340px;display:flex;gap:16px}
.step h3{font-size:14px;font-weight:800;color:var(--navy);margin:8px 0 12px;line-height:1.3}
.step p{font-size:13.5px;font-weight:700;color:var(--muted);line-height:1.45}

/* why */
.why{left:0;top:1262px;width:1200px;height:415px;background:linear-gradient(90deg,#eef0f4 0%,#f8f8fa 40%,#dcdde2 80%,#b9bac0 100%)}
.why-title{left:0;top:1314px;width:1200px;text-align:center;font-weight:800;font-size:30px;color:var(--navy)}
.why-title em{font-style:normal;color:var(--red-bright)}
.why-list{left:140px;top:1392px;list-style:none}
.why-list li{display:flex;align-items:center;gap:12px;font-size:13.5px;color:#3b3f4a;height:32px;white-space:nowrap}
.why-list b{color:#22262f}
.why-list .arrow{width:20px;height:20px;border-radius:50%;background:var(--red-bright);flex:none}

/* faq */
.faq-media{left:80px;top:1807px;width:520px;height:416px;background:linear-gradient(160deg,#5d8fd0 0%,#c8d8ec 35%,#b62c2c 60%,#3a6b2a 100%)}
.faq-list{left:633px;top:1807px;width:489px}
.faq-item{border:1px solid var(--line);border-radius:8px;height:42px;margin-bottom:10px;padding:0 14px;display:flex;align-items:center;justify-content:space-between;font-weight:700;font-size:14.5px;color:var(--navy)}
.faq-item .chev{width:9px;height:9px;border-right:2px solid var(--navy);border-bottom:2px solid var(--navy);transform:rotate(45deg) translateY(-3px)}
.faq-item.open{height:auto;display:block;padding:12px 14px 16px}
.faq-item.open .q{display:flex;justify-content:space-between;align-items:center}
.faq-item.open .chev{transform:rotate(-135deg)}
.faq-item.open p{font-weight:400;font-size:13.5px;color:var(--muted);line-height:1.45;margin-top:8px}

/* footer */
.site-footer{left:0;top:2288px;width:1200px;height:457px;background:linear-gradient(180deg,#1a3ea8 0%,#0f2d86 40%,#0a1f5c 100%)}
.footer-brand{left:0;top:2348px;width:1200px;display:flex;justify-content:center;align-items:center;gap:16px}
.footer-col h4{color:var(--white);font-size:15px;font-weight:800;margin-bottom:22px;white-space:nowrap}
.footer-col p,.footer-col a{color:var(--white);font-size:13px;font-weight:600;line-height:1.38;display:block;text-decoration:none}
.trust{width:150px;height:48px;background:var(--white);border-radius:4px;margin-bottom:12px}
.footer-call{left:779px;top:2460px;width:386px;height:122px;border:3px solid var(--white);border-radius:12px;padding:0 16px;justify-content:center}
.legal{left:0;top:2745px;width:1200px;height:41px;background:var(--white);text-align:center;font-size:12.5px;font-weight:700;padding-top:12px;color:#333}
</style>
</head>
<body>

<header class="site-header abs">
  <div class="brand abs"><span class="brand-dot"></span><span class="brand-name">Hulls for Heroes</span></div>
  <div class="call-box header-call abs">
    <div class="ring"><svg width="32" height="32" viewBox="0 0 24 24"><path fill="#fff" d="M6.6 10.8a15 15 0 0 0 6.6 6.6l2.2-2.2c.3-.3.7-.4 1-.2 1.1.4 2.3.6 3.6.6.6 0 1 .4 1 1V20c0 .6-.4 1-1 1A17 17 0 0 1 3 4c0-.6.4-1 1-1h3.5c.6 0 1 .4 1 1 0 1.3.2 2.5.6 3.6.1.3 0 .7-.2 1z"/></svg></div>
    <div><div class="lead">CALL TODAY TO DONATE</div><div class="num">1-800-555-0142</div><div class="note">Live Operators Available - 7 Days A Week</div></div>
  </div>
</header>

<nav class="main-nav abs">
  <a style="left:178px">HOW TO DONATE</a>
  <a style="left:365px">WHY DONATE</a>
  <a style="left:525px">FAQ</a>
  <a style="left:609px">ABOUT</a>
</nav>

<section class="hero-media abs" role="img" aria-label="Soldier in camouflage hugging a child holding a small flag, beside a motor yacht over a sketched city skyline"></section>
<div class="donate-tab abs">DONATE YOUR BOATS ONLINE</div>

<form class="donate-form abs">
  <h2>Full Tax Deduction - Running or Not</h2>
  <div class="field-row"><div class="field">First Name</div><div class="field">Last Name</div></div>
  <div class="field-row"><div class="field">Daytime Phone</div><div class="field">Email</div></div>
  <div class="field-row"><div class="field">Pickup Address</div></div>
  <div class="field-row"><div class="field">Pickup City</div></div>
  <div class="field-row"><div class="field select">Pickup State</div><div class="field">Zip Code</div></div>
  <div class="field-row"><div class="field select">Choose Year</div><div class="field select">Choose Make</div></div>
  <div class="field-row"><div class="field">Vehicle Model</div></div>
  <div class="btn-donate">DONATE NOW</div>
</form>

<section class="promo-band abs"></section>
<div class="promo-badge abs">
  <div class="s">DONATE YOUR BOATS TO</div>
  <div class="b">VETERANS</div>
  <div class="s">MAKE A DIFFERENCE</div>
</div>
<div class="benefit abs" style="left:551px;top:730px"><svg width="62" height="62" viewBox="0 0 62 62"><circle cx="31" cy="31" r="27" fill="none" stroke="#fff" stroke-width="4"/><path d="M18 31l9 9 17-18" fill="none" stroke="#fff" stroke-width="5"/></svg>You have<br>no costs</div>
<div class="benefit abs" style="left:703px;top:730px"><svg width="62" height="62" viewBox="0 0 62 62"><path d="M6 36h50l-8 10H14z M20 36l6-10h14l6 10z" fill="#fff"/></svg>Free pickup,<br>running or not</div>
<div class="benefit abs" style="left:855px;top:730px"><svg width="62" height="62" viewBox="0 0 62 62"><rect x="16" y="6" width="30" height="50" fill="none" stroke="#fff" stroke-width="3"/><path d="M22 18h18M22 42h18M22 48h18" stroke="#fff" stroke-width="3"/><text x="31" y="35" font-size="14" font-weight="800" fill="#fff" text-anchor="middle" font-family="Open Sans,sans-serif">$</text></svg>We issue you an<br>IRS tax receipt</div>
<div class="benefit abs" style="left:1007px;top:730px"><svg width="62" height="62" viewBox="0 0 62 62"><rect x="18" y="8" width="32" height="44" fill="none" stroke="#fff" stroke-width="3"/><path d="M25 20h18M25 28h18M25 36h18" stroke="#fff" stroke-width="3"/><circle cx="18" cy="46" r="9" fill="none" stroke="#fff" stroke-width="3"/></svg>We take care of<br>all paperwork.</div>

<h2 class="section-title abs" style="top:974px"><span>HOW TO <em>DONATE</em></span></h2>
<div class="step abs" style="left:78px;top:1050px">
  <svg width="70" height="96" viewBox="0 0 70 96" style="flex:none"><rect x="0" y="0" width="70" height="14" fill="#0d2a7a"/><rect x="22" y="22" width="48" height="14" fill="#0d2a7a"/><rect x="0" y="44" width="70" height="14" fill="#0d2a7a"/><circle cx="12" cy="76" r="9" fill="#0d2a7a"/></svg>
  <div><h3>CALL US AT 1-800-555-0142 OR<br>FILL OUT THE ONLINE FORM</h3><p>Donating your boat is easy and donation is accepted nationwide.</p></div>
</div>
<div class="step abs" style="left:446px;top:1070px">
  <svg width="84" height="50" viewBox="0 0 84 50" style="flex:none"><path d="M0 26h84l-12 20H12z M22 26l8-14h22l8 14z" fill="#9b1c1c"/></svg>
  <div><h3 style="margin-top:20px">WE PICK UP THE BOAT</h3><p>Any boats is accepted and we will arrange to pick up your boat when it is most convenient for you.</p></div>
</div>
<div class="step abs" style="left:848px;top:1050px">
  <svg width="74" height="80" viewBox="0 0 74 80" style="flex:none"><rect x="4" y="4" width="66" height="72" fill="none" stroke="#0d2a7a" stroke-width="3"/><rect x="14" y="12" width="46" height="24" fill="none" stroke="#0d2a7a" stroke-width="2"/><text x="37" y="31" font-size="18" font-weight="800" fill="#0d2a7a" text-anchor="middle" font-family="Open Sans,sans-serif">$</text><path d="M14 46h46M14 56h46M14 66h46" stroke="#0d2a7a" stroke-width="2"/></svg>
  <div><h3 style="margin-top:38px">TAX WRITE-OFF</h3><p>Once the boat donation is complete, you will receive your tax deductable boat donation receipt.</p></div>
</div>

<section class="why abs" role="img" aria-label="Soldier kneeling among flags at a memorial, faded behind the text"></section>
<h2 class="why-title abs">WHY DONATE <em>YOUR BOATS TO US</em></h2>
<ul class="why-list abs">
  <li><span class="arrow"></span><span><b>Top Rated Charity &amp; IRS 501(c)3 Approved :</b> Free 24/7 Pickup with No DMV Hassles.</span></li>
  <li><span class="arrow"></span><span><b>Free Local Towing :</b> We will pick up your boat donation, running or not, when it's most convenient.</span></li>
  <li><span class="arrow"></span><span><b>All Boats Accepted :</b> We take your car regardless of its condition or registration status.</span></li>
  <li><span class="arrow"></span><span><b>Income Tax Deduction :</b> We issue you an IRS tax receipt &amp; offer the largest resale network to get you the highest tax write-off possible.</span></li>
  <li><span class="arrow"></span><span><b>No Paperwork Hassles :</b> We take any boat and handle everything: DMV, Smog and IRS paperwork.</span></li>
  <li><span class="arrow"></span><span><b>Boat donations help fund programs :</b> And benefit Harbor Veterans Relief Fund. An IRS 501(c)3 nonprofit organization.</span></li>
  <li><span class="arrow"></span><span><b>Schedule a Free Pickup :</b> Complete the form and a representative will call you to arrange a convenient time to pickup your boat.</span></li>
</ul>

<h2 class="section-title abs" style="top:1730px"><span>FREQUENTLY ASKED <em>QUESTIONS</em></span></h2>
<div class="faq-media abs" role="img" aria-label="Rows of American flags planted in a grassy field under a blue sky"></div>
<div class="faq-list abs">
  <div class="faq-item">What types of boats can be donated?<span class="chev"></span></div>
  <div class="faq-item open"><div class="q">What paperwork do I need to donate my boat?<span class="chev"></span></div><p>All you need is a title, free of all liens. We will request some general information from you at the time of donation such as, the year, make, and model of the boat, as well as its general mechanical condition. We accept all boats, running or non-running.</p></div>
  <div class="faq-item">Is my donated boat tax -deductible?<span class="chev"></span></div>
  <div class="faq-item">What if the boat is not registered in my name?<span class="chev"></span></div>
  <div class="faq-item">How much will I receive as a tax deduction for my boat?<span class="chev"></span></div>
  <div class="faq-item">When will I receive my tax receipt?<span class="chev"></span></div>
  <div class="faq-item">How do I schedule a pick up?<span class="chev"></span></div>
</div>

<footer class="site-footer abs"></footer>
<div class="footer-brand abs"><span class="brand-dot"></span><span class="brand-name">Hulls for Heroes</span></div>
<div class="footer-col abs" style="left:72px;top:2462px;width:240px">
  <h4>ABOUT HULLS FOR HEROES</h4>
  <p>We turn donated boats into real support for veterans and their families. Every hull we collect funds care, housing help and job programs, and our team handles pickup, paperwork and receipts for you at no cost.</p>
</div>
<div class="footer-col abs" style="left:380px;top:2462px">
  <h4>NAVIGATION</h4>
  <a>HOW TO DONATE</a><a>WHY DONATE</a><a>FAQ</a><a>ABOUT</a>
</div>
<div class="footer-col abs" style="left:555px;top:2462px">
  <h4>SAFE &amp; SECURE</h4>
  <div class="trust"></div>
  <div class="trust" style="width:120px;height:40px"></div>
  <div class="trust" style="width:40px;height:40px;border-radius:50%"></div>
</div>
<div class="call-box footer-call abs">
  <div class="ring"><svg width="32" height="32" viewBox="0 0 24 24"><path fill="#fff" d="M6.6 10.8a15 15 0 0 0 6.6 6.6l2.2-2.2c.3-.3.7-.4 1-.2 1.1.4 2.3.6 3.6.6.6 0 1 .4 1 1V20c0 .6-.4 1-1 1A17 17 0 0 1 3 4c0-.6.4-1 1-1h3.5c.6 0 1 .4 1 1 0 1.3.2 2.5.6 3.6.1.3 0 .7-.2 1z"/></svg></div>
  <div><div class="lead">CALL TODAY TO DONATE</div><div class="num">1-800-555-0142</div><div class="note">Live Operators Available - 7 Days A Week</div></div>
</div>
<div class="legal abs">COPYRIGHT © 2017 HULLS FOR HEROES. PRIVACY POLICY I TERMS &amp; CONDITIONS. ALL RIGHTS RESERVED.</div>

</body>
</html>
```